International Petrochemical business needs a web design for Clearway Desk system

We need a web design for a "Clearway Desk" system for an international petrochemical company. The web site is used internally within the company. It is hosted by an internal department which provides government permit request service for other departments.

We would like to see designs of two pages using color light blue. (home page, internal page as attached).
Home Page:
1. Header has a background image and small animation. Header on home page can be taller than the header of the internal page.
2. Layout as attached.

Internal Page:
1. Header can use the same background image as the home page and can be shorter to utilize the page for content.
2. The blue icon behind every captions represent an icon. When user move mouse over this icon, it displays the caption in Thai language as a tooltip. This icon needs to be redesign.

The final design should communicate the followings:
- Excellent service provided system in terms of time and accurary
- Rapid growth of business via building petrochemical refinery plant
Updates

For Internal Page, the blue circle behind every captions represent an icon. When mouse over this icon, a tool tip showing the caption in Thai language is shown. Please also design this icon..

There are more feedbacks from customer as followed:

1. Banner should consists of 
    1.1 "Approved" stamp on paper
    1.2 An image of Garuda. It is used on every government documents in Thailand
    1.3 Image of petrochemical plant
2. Each menu item (Home, Permit, Search, etc) should have different colors. Drop down menu will use the same color as its parent menu item.
3. Overall tone of the web page should be light blue with background of the body the web page in white
4. "New Request" button should use green color with icon on it
5. Table header of each box in the body of the page should use dark blue background with text in white

Please kindly submit your revisions.
Thank you.

Industry/Entity Type

Business

Requirements
Must have
• 1. Design for 1024x768 screen resolution
2. Use light blue theme
3. Background of header where the company logo is must have white background

```html
<!DOCTYPE html>
<html lang="en">
<head>
<meta charset="utf-8">
<title>Clearway Desk</title>
<link href="https://fonts.googleapis.com/css2?family=Source+Sans+3:wght@400;600;700&display=swap" rel="stylesheet">
<style>
:root{
  --sky:#27b2ea;
  --sky-light:#45c3f2;
  --sky-dark:#1a9fd6;
  --red:#e8242b;
  --red-dark:#c9141b;
  --row-a:#edf4f8;
  --row-b:#f6f9fb;
  --ink:#333;
  --ink-soft:#555;
  --navy:#2a2a7a;
  --rule:#e4e8ec;
  --foot:#050505;
  --white:#fff;
}
*{box-sizing:border-box;margin:0;padding:0}
html,body{width:776px;height:1200px;overflow:hidden;background:var(--white)}
body{position:relative;font-family:"Source Sans 3",sans-serif;color:var(--ink)}
.abs{position:absolute}

.brand{left:66px;top:28px;display:flex;align-items:center;gap:6px}
.brand-dot{width:18px;height:18px;border-radius:50%;background:var(--sky-dark)}
.brand-name{font-weight:700;font-size:12px;color:var(--sky-dark);letter-spacing:.3px}
.system-name{left:241px;top:44px;font-size:12.5px;color:var(--navy)}

.main-nav{left:56px;top:86px;width:663px;height:31px;display:flex;border-radius:3px;
  background:linear-gradient(var(--sky-light),var(--sky-dark));box-shadow:0 6px 8px -4px rgba(0,0,0,.25)}
.main-nav a{color:var(--white);text-decoration:none;font-size:12px;display:flex;align-items:center;justify-content:center;
  border-right:1px solid rgba(255,255,255,.25)}
.main-nav a:last-child{border-right:0}
.main-nav .active{background:linear-gradient(var(--red),var(--red-dark))}
.dropdown{left:143px;top:117px;width:126px;height:71px;background:linear-gradient(var(--red),var(--red-dark));
  border-radius:0 0 3px 3px;padding:4px 12px;box-shadow:0 3px 6px rgba(0,0,0,.25);z-index:2}
.dropdown a{display:block;color:var(--white);text-decoration:none;font-size:10px;line-height:21px;border-bottom:1px solid rgba(0,0,0,.12)}
.dropdown a:last-child{border-bottom:0}

.banner{left:56px;top:137px;width:663px;height:190px;
  background:radial-gradient(ellipse at 70% 35%,#e9f6ff 0%,#8fc7ef 22%,#2a6fbf 55%,#0c2f78 100%)}
.banner-dots{left:672px;top:310px;display:flex;gap:2px}
.banner-dots i{width:8px;height:8px;border-radius:50%;border:1.5px solid #dde;background:transparent}
.banner-dots i:first-child{background:#dde}

.section-title{font-size:11.5px;font-weight:600;color:#333}

.panel{background:var(--row-b)}
.t-head,.t-row{display:grid;align-items:center}
.t-head{height:35px;background:linear-gradient(90deg,var(--sky-dark),var(--sky-light) 50%,var(--sky-dark));color:var(--white);font-size:12px;font-weight:600}
.t-row{height:35.5px;font-size:8px;color:var(--ink-soft)}
.t-row:nth-child(even){background:var(--row-a)}
.t-row:nth-child(odd){background:var(--row-b)}
.status{display:inline-block;width:7px;height:7px;border-radius:50%;margin-left:5px;vertical-align:-1px}
.status.ok{background:#3aa535}
.status.warn{background:#f0b41c}

.pager{display:flex;gap:4px;height:16px}
.pager span{min-width:16px;height:16px;padding:0 4px;display:flex;align-items:center;justify-content:center;font-size:8px;color:#333;
  background:linear-gradient(#fff,#e5e5e5);border:1px solid #ccc;border-radius:2px}
.pager .wide{min-width:29px}

.rule{height:1px;background:var(--rule);left:56px;width:663px}

.new-request{left:501px;top:844px;width:153px;height:30px;border-radius:3px;
  background:linear-gradient(#5a5a5a,#111 55%,#000);color:var(--white);font-weight:700;font-size:11.5px;
  display:flex;align-items:center;justify-content:center;box-shadow:0 2px 3px rgba(0,0,0,.4)}

.site-footer{left:0;top:1132px;width:776px;height:68px;background:var(--foot);color:var(--white)}
.foot-links{left:86px;top:17px;font-size:8px}
.foot-copy{left:86px;top:42px;font-size:8px}
.social{left:566px;top:24px;display:flex;gap:10px}
.social i{width:21px;height:21px;border-radius:3px;background:#ddd}
</style>
</head>
<body>

<header>
  <div class="abs brand"><span class="brand-dot"></span><span class="brand-name">NORVANE CHEMICAL</span></div>
  <div class="abs system-name">Clearway Desk</div>
  <nav class="abs main-nav">
    <a style="width:87px;justify-content:flex-start;padding-left:14px">Home</a>
    <a class="active" style="width:126px">Permits</a>
    <a style="width:123px">Search</a>
    <a style="width:124px">Report</a>
    <a style="width:120px">Admin</a>
    <a style="width:83px;justify-content:flex-end;padding-right:16px">Help</a>
  </nav>
  <div class="abs dropdown">
    <a>Create New Permit</a>
    <a>Transfer Role</a>
    <a>Transfer Res. Person</a>
  </div>
  <div class="abs banner" role="img" aria-label="Blue digital banner with streams of binary numbers and light trails"></div>
  <div class="abs banner-dots"><i></i><i></i><i></i><i></i></div>
</header>

<main>
  <h2 class="abs section-title" style="left:59px;top:357px">New Requests</h2>
  <div class="abs panel" style="left:56px;top:384px;width:309px">
    <div class="t-head" style="grid-template-columns:124px 139px 1fr;padding-left:9px"><span>Request No.</span><span>Requested &nbsp;Date</span><span>Branch</span></div>
    <div>
      <div class="t-row" style="grid-template-columns:117px 139px 1fr;padding-left:9px"><span>56-0003</span><span>20/4/2013</span><span>GC1</span></div>
      <div class="t-row" style="grid-template-columns:117px 139px 1fr;padding-left:9px"><span>56-0004</span><span>21/4/2013</span><span>GC2</span></div>
      <div class="t-row" style="grid-template-columns:117px 139px 1fr;padding-left:9px"><span>56-0004</span><span>21/4/2013</span><span>GC3</span></div>
    </div>
  </div>
  <div class="abs pager" style="left:158px;top:549px"><span class="wide">PREV</span><span>1</span><span>2</span><span>3</span><span>4</span><span>5</span><span>6</span><span>....</span><span class="wide">NEXT</span></div>

  <h2 class="abs section-title" style="left:412px;top:357px">My Working Requests</h2>
  <div class="abs panel" style="left:411px;top:384px;width:308px">
    <div class="t-head" style="grid-template-columns:103px 139px 1fr;padding-left:8px"><span>Request No.</span><span>Requested &nbsp;Date</span><span>Status</span></div>
    <div>
      <div class="t-row" style="grid-template-columns:116px 91px 1fr;padding-left:9px"><span>55-0200</span><span>20/4/2013</span><span>Waiting for Progress</span></div>
      <div class="t-row" style="grid-template-columns:116px 91px 1fr;padding-left:9px"><span>55-0210</span><span>24/3/2013</span><span>In Progress</span></div>
      <div class="t-row" style="grid-template-columns:116px 91px 1fr;padding-left:9px"><span>55-0300</span><span>18/1/2013</span><span>Incomplete Document</span></div>
      <div class="t-row" style="grid-template-columns:116px 91px 1fr;padding-left:9px"><span>55-0301</span><span>18/1/2013</span><span>Cancel Requested</span></div>
    </div>
  </div>
  <div class="abs pager" style="left:514px;top:580px"><span class="wide">PREV</span><span>1</span><span>2</span><span>3</span><span>4</span><span>5</span><span>6</span><span>....</span><span class="wide">NEXT</span></div>

  <div class="abs rule" style="top:616px"></div>

  <h2 class="abs section-title" style="left:59px;top:633px">Expiring Permits</h2>
  <div class="abs panel" style="left:56px;top:660px;width:663px">
    <div class="t-head" style="grid-template-columns:107px 116px 121px 89px 160px 1fr;padding-left:9px"><span>Permit No.</span><span>Expire &nbsp;Date</span><span>Permit Name</span><span>Branch</span><span>Required Time (Day)</span><span>Due Date</span></div>
    <div>
      <div class="t-row" style="grid-template-columns:107px 116px 121px 89px 165px 1fr;padding-left:10px"><span>AB56001</span><span>20/4/2013</span><span>Permit Name ###10</span><span>GC1</span><span>30<i class="status ok"></i></span><span>-40</span></div>
      <div class="t-row" style="grid-template-columns:107px 116px 121px 89px 165px 1fr;padding-left:10px"><span>AB56001</span><span>20/4/2013</span><span>Permit Name ###10</span><span>GC1</span><span>30<i class="status warn"></i></span><span>-40</span></div>
    </div>
  </div>
  <div class="abs pager" style="left:511px;top:786px"><span class="wide">PREV</span><span>1</span><span>2</span><span>3</span><span>4</span><span>5</span><span>6</span><span>....</span><span class="wide">NEXT</span></div>

  <div class="abs rule" style="top:822px"></div>

  <h2 class="abs section-title" style="left:59px;top:840px">My In Progress Requests</h2>
  <div class="abs panel" style="left:56px;top:869px;width:309px">
    <div class="t-head" style="grid-template-columns:116px 139px 1fr;padding-left:9px"><span>Request No.</span><span>Requested &nbsp;Date</span><span>Status</span></div>
    <div>
      <div class="t-row" style="grid-template-columns:117px 139px 1fr;padding-left:9px"><span>56-0001</span><span>20/4/2013</span><span>GC1</span></div>
      <div class="t-row" style="grid-template-columns:117px 137px 1fr;padding-left:9px"><span>56-0002</span><span>21/4/2013</span><span>GC2</span></div>
      <div class="t-row" style="grid-template-columns:117px 137px 1fr;padding-left:9px"><span>56-0002</span><span>21/4/2013</span><span>GC2</span></div>
      <div class="t-row" style="grid-template-columns:117px 137px 1fr;padding-left:9px"><span>56-0002</span><span>21/4/2013</span><span>GC2</span></div>
    </div>
  </div>
  <div class="abs pager" style="left:158px;top:1078px"><span class="wide">PREV</span><span>1</span><span>2</span><span>3</span><span>4</span><span>5</span><span>6</span><span>....</span><span class="wide">NEXT</span></div>

  <div class="abs new-request">NEW REQUEST</div>

  <h2 class="abs section-title" style="left:408px;top:892px">Recent Completed Requests</h2>
  <div class="abs panel" style="left:410px;top:919px;width:309px">
    <div class="t-head" style="grid-template-columns:194px 1fr;padding-left:9px"><span>Request No.</span><span>Completed &nbsp;Date</span></div>
    <div>
      <div class="t-row" style="grid-template-columns:183px 1fr;padding-left:9px"><span>56-0001</span><span>20/4/2013</span></div>
      <div class="t-row" style="grid-template-columns:183px 1fr;padding-left:9px"><span>56-0002</span><span>21/4/2013</span></div>
      <div class="t-row" style="grid-template-columns:116px 139px 1fr;padding-left:9px"><span>56-0004</span><span>21/4/2013</span><span>GC3</span></div>
    </div>
  </div>
  <div class="abs pager" style="left:513px;top:1078px"><span class="wide">PREV</span><span>1</span><span>2</span><span>3</span><span>4</span><span>5</span><span>6</span><span>....</span><span class="wide">NEXT</span></div>
</main>

<footer class="abs site-footer">
  <div class="abs foot-links">HOME | ABOUT US | PUBLISHERS | AUTHORS | CONTACT</div>
  <div class="abs foot-copy">Copyrights 2013. All Rights Reserved.</div>
  <div class="abs social"><i></i><i></i><i></i><i></i></div>
</footer>

</body>
</html>
```